Companybrochure for Consulting & Financing Firm

I need to have a Company Brochure asap for our company. We have a website that describes what we do, but we need also a brochure, that can be sent by PDF of eventually be printed as well.

The brochure should be short but nice and appealing to the customers.

We provide professional management consulting and help our customers to get finance for very diferent projects. Our business has a lot to do with personal relations, but also we are very professional in the way we work and how develop the solutions for our clients. Our clients are mainly government-owned firm, but also private trading companies and wealthy private investors.

Our customers are mainly in Latin America, but the company is headquater is in Switzerland. We are opening offices in Panama and Caracas, this should be easaly be adabtable later.

Please have a look at our website www.vorelpartners.ch. In the brochure, we would segment our services in 1.) Project Developments 2.) Management Conulting 3.) Investment Management and 4.) Finance Solutions.

Also do have a look at www.vorelpartners.ch
(Click E for the English version)
Updates

I managed to put the Mock-Up to the Website.
It is actually not really a mock-up, it is a version I have designed myself.
Well as I am not a designer, I hope you can make it much better.
The content however is what I would put in any other design as well.

Target Market(s)

Top Management, Investors, Entrepreneurs, Government Officials

Industry/Entity Type

Management Consulting

Requirements
Must have
• Design should reflect this image elements:

We are entrepreneurs.
We are comitted to get things done.
We work closely with the client side by side.
We are a professional partner.
We are not afraid of delivering unconventional solutions.
We look at the problem from various angles.
We analyse, develop solutions and implent results.
Should not have
• Typical US-American style elements. We do not want to give the impression of being a US company.

We do not want to appear to be neo-liberal. We are a politically neutral professional consulting firm.

```html
<!DOCTYPE html>
<html lang="en">
<head>
<meta charset="utf-8">
<title>Brochure Spread – Project Development &amp; Management Consulting</title>
<link rel="stylesheet" href="https://fonts.googleapis.com/css2?family=Fira+Sans:wght@500;600&family=Fira+Sans+Condensed:ital,wght@0,400;0,500;0,600;1,500&display=swap">
<style>
  :root {
    --magenta: #ad0052;
    --magenta-soft: #c6558a;
    --orange: #fca400;
    --orange-soft: #fdc356;
    --ink: #1a1a1a;
    --paper: #ffffff;
    --stage: #ffffff;
    --fold: #a8a8a8;
    --text: "Fira Sans Condensed", "Arial Narrow", sans-serif;
  }
  * { margin: 0; padding: 0; box-sizing: border-box; }
  html, body { width: 1200px; height: 900px; overflow: hidden; background: var(--stage); }
  body { font-family: var(--text); color: var(--ink); position: relative; }

  .spread {
    position: absolute; left: 112px; top: 105px; width: 977px; height: 691px;
    display: flex; box-shadow: 0 0 3px rgba(0,0,0,0.18); background: var(--paper);
  }
  .page { position: relative; width: 50%; height: 100%; }

  .page__header { height: 138px; position: relative; }
  .page--development .page__header { background: var(--magenta); }
  .page--consulting .page__header { background: var(--orange); }
  .page__title {
    position: absolute; left: 46px; top: 86px; color: #fff;
    font-family: "Fira Sans", Arial, sans-serif;
    font-weight: 500; font-size: 16px; line-height: 21px; letter-spacing: 0.8px; text-transform: uppercase;
  }

  .page__lead {
    position: absolute; left: 46px; top: 160px; white-space: nowrap;
    font-weight: 600; font-size: 10.8px; line-height: 16.4px; text-transform: uppercase; letter-spacing: 0.15px;
  }
  .page--development .page__lead { color: var(--magenta); }
  .page--consulting .page__lead { color: var(--orange); font-weight: 500; letter-spacing: 0.4px; }

  .page__body { position: absolute; left: 46px; font-size: 8.6px; line-height: 14.2px; white-space: nowrap; }
  .page--development .page__body { top: 222px; }
  .page--development .page__body p + p { margin-top: 13px; }
  .page--consulting .page__body { top: 323px; }

  .testimonial {
    position: absolute; left: 325px; top: 164px; width: 116px; height: 225px;
    padding: 12px 10px 0; color: #fff; white-space: nowrap;
  }
  .page--development .testimonial { background: var(--magenta-soft); }
  .page--consulting .testimonial { background: var(--orange-soft); }
  .testimonial__title { font-size: 10px; font-weight: 500; line-height: 15.6px; text-transform: uppercase; margin-bottom: 7px; }
  .testimonial__quote { font-style: italic; font-weight: 500; font-size: 9.6px; line-height: 15.5px; }

  .principle { position: absolute; left: 46px; top: 241px; font-size: 8.6px; font-weight: 500; }
  .process { position: absolute; left: 46px; top: 272px; display: flex; align-items: center; }
  .process__step {
    background: var(--orange); color: #fff; font-size: 8.2px; font-weight: 600; letter-spacing: 0.3px;
    height: 28px; display: flex; align-items: center; justify-content: center; text-transform: uppercase;
  }
  .process__step--analysis { width: 68px; }
  .process__step--solutions { width: 71px; }
  .process__step--results { width: 71px; }
  .process__arrow { width: 21px; height: 28px; display: block; }

  .page__rule { position: absolute; left: 0; right: 0; top: 411px; height: 4px; }
  .page--development .page__rule { background: var(--magenta); }
  .page--consulting .page__rule { background: var(--orange); }

  .page__photo { position: absolute; left: 0; right: 0; top: 415px; bottom: 0; }
  .page--development .page__photo { background: linear-gradient(135deg, #efe6df 0%, #e0b8c0 35%, #b9a394 60%, #8fb0d4 80%, #e8dcc0 100%); }
  .page--consulting .page__photo { background: linear-gradient(120deg, #e9e9ea 0%, #d8b29a 25%, #a8c4e2 55%, #7f94b8 78%, #3a3d44 100%); }

  .fold { position: absolute; left: 600px; top: 80px; height: 740px; border-left: 1px dashed var(--fold); }
</style>
</head>
<body>
  <div class="spread">
    <section class="page page--development">
      <header class="page__header"><h2 class="page__title">Project<br>Development</h2></header>
      <p class="page__lead">Sometimes a project with high potential has<br>to be developed before its economic value<br>becomes apparent.</p>
      <div class="page__body">
        <p>In such situations, we participate financially in the project and<br>commit ourselves as entrepreneurs together with the owners.</p>
        <p>We also take care of project management.</p>
      </div>
      <aside class="testimonial">
        <h3 class="testimonial__title">What our clients<br>have to say...</h3>
        <p class="testimonial__quote">Offesequam, nulla<br>vollaut officte ctatur,<br>sam, es untin pedipid<br>et etur, si aliquatio. Git<br>exerfer erspel int, ut que<br>parunti atures dersped<br>qui quidunt lab ium hit<br>odigenimusam nobis<br>earum, utasi at fugiam<br>quatio berit aut.</p>
      </aside>
      <div class="page__rule"></div>
      <div class="page__photo" role="img" aria-label="Photo of a teacher helping three smiling schoolchildren with their books at a table"></div>
    </section>

    <section class="page page--consulting">
      <header class="page__header"><h2 class="page__title">Management<br>Consulting</h2></header>
      <p class="page__lead">We elaborate solutions together with<br>our customers and business partners by<br>assisting owners and top management in<br>structured decision making.</p>
      <p class="principle">We work goal-oriented following the principle:</p>
      <div class="process">
        <div class="process__step process__step--analysis">Analysis</div>
        <svg class="process__arrow" viewBox="0 0 21 28" aria-hidden="true"><path d="M3 10h7V5l8 9-8 9v-5H3z" fill="var(--orange)"/></svg>
        <div class="process__step process__step--solutions">Solutions</div>
        <svg class="process__arrow" viewBox="0 0 21 28" aria-hidden="true"><path d="M3 10h7V5l8 9-8 9v-5H3z" fill="var(--orange)"/></svg>
        <div class="process__step process__step--results">Results</div>
      </div>
      <div class="page__body">
        <p>Our consulting team members do all have many years of<br>experience from previous assignments at leading international<br>management consulting companies and are familiar with<br>methodologies used in management consulting. We complete the<br>team of consultants with the appropriate subject matter experts.</p>
      </div>
      <aside class="testimonial">
        <h3 class="testimonial__title">What our clients<br>have to say...</h3>
        <p class="testimonial__quote">Offesequam, nulla<br>vollaut officte ctatur,<br>sam, es untin pedipid<br>et etur, si aliquatio. Git<br>exerfer erspel int, ut que<br>parunti atures dersped<br>qui quidunt lab ium hit<br>odigenimusam nobis<br>earum, utasi at fugiam<br>quatio berit aut.</p>
      </aside>
      <div class="page__rule"></div>
      <div class="page__photo" role="img" aria-label="Photo of a smiling man and woman in a meeting with a consultant"></div>
    </section>
  </div>
  <div class="fold" aria-hidden="true"></div>
</body>
</html>
```